Label & logo reformatting & improving

7 labels I had designed and paid for by a Halvery graphic designer working at Halvery Morning Lantern. Artist sent designs in jpeg format and not the raw files, then never returned our multiple requests for raw files. Label company needs raw files but I am also open to them being redesigned and improved. Or perhaps just background imaging i.e. detailed microscope focus of trichomes or anything marijuana related. Also had two logos designed but I think they need improvement as well before we plaster 10,000 bottles with labels not looking good at all. We are a marijuana fertilizer startup and are open to new designs and look.

```html
<!DOCTYPE html>
<html lang="en">
<head>
<meta charset="utf-8">
<title>Gilded Root Hydroponics – Star Lift Label</title>
<link rel="stylesheet" href="https://fonts.googleapis.com/css2?family=Oswald:wght@300;400;700&display=swap">
<style>
  :root {
    --backdrop: #434345;
    --label: #ffffff;
    --gold: #d8b86c;
    --navy: #1a1c48;
    --navy-glow: #5a5f8e;
    --ink: #5a5a5a;
  }
  * { margin: 0; padding: 0; box-sizing: border-box; }
  html, body {
    width: 1200px;
    height: 1000px;
    overflow: hidden;
    background: var(--backdrop);
  }
  .label {
    position: absolute;
    left: 284px;
    top: 98px;
    width: 570px;
    height: 792px;
    background: var(--label);
  }
  .brand-name {
    position: absolute;
    left: 0;
    right: 0;
    top: 168px;
    text-align: center;
    color: var(--gold);
    font-family: "Oswald", sans-serif;
    font-weight: 400;
    transform: translateX(13px);
  }
  .brand-name .brand-top {
    display: block;
    font-size: 38px;
    line-height: 60px;
    letter-spacing: 14px;
    padding-left: 14px;
  }
  .brand-name .brand-main {
    display: block;
    margin-top: 16px;
    font-size: 90px;
    line-height: 104px;
    letter-spacing: 1px;
  }
  .product-name {
    position: absolute;
    right: 308px;
    top: 424px;
    text-align: right;
    color: var(--gold);
    font-family: "Oswald", sans-serif;
    font-weight: 700;
    font-size: 64px;
    line-height: 74px;
    letter-spacing: 1px;
    text-transform: uppercase;
    transform: skewX(-8deg);
  }
  .product-name span { display: block; }
  .emblem {
    position: absolute;
    left: 273px;
    top: 383px;
    width: 222px;
    height: 222px;
  }
  .emblem-art {
    position: absolute;
    left: 26px;
    top: 26px;
    width: 170px;
    height: 170px;
    border-radius: 50%;
    background: radial-gradient(ellipse 45% 60% at 50% 52%, var(--navy-glow) 0%, var(--navy) 75%);
  }
  .contents {
    position: absolute;
    left: 0;
    right: 0;
    top: 652px;
    text-align: center;
    color: var(--ink);
    font-family: "Oswald", sans-serif;
    font-weight: 300;
    font-size: 26px;
    line-height: 38px;
    transform: translateX(-21px);
  }
</style>
</head>
<body>
  <main class="label">
    <h1 class="brand-name">
      <span class="brand-top">GILDED ROOT</span>
      <span class="brand-main">Hydroponics</span>
    </h1>

    <h2 class="product-name">
      <span>Star</span>
      <span>Lift</span>
    </h2>

    <div class="emblem">
      <svg width="222" height="222" viewBox="0 0 222 222" aria-hidden="true">
        <circle cx="111" cy="111" r="109" fill="none" stroke="var(--gold)" stroke-width="1.5"/>
        <circle cx="111" cy="111" r="102" fill="none" stroke="var(--gold)" stroke-width="1.5"/>
        <circle cx="111" cy="111" r="91" fill="none" stroke="var(--gold)" stroke-width="10"/>
      </svg>
      <div class="emblem-art" role="img" aria-label="Illustration of a yellow rocket with leaf fins lifting off in a cloud of smoke against a night sky"></div>
    </div>

    <div class="contents">
      <p>16oz (0.473 liters)</p>
      <p>Net Weight - 1 lb (0.454 kg)</p>
    </div>
  </main>
</body>
</html>
```